RWT Fittings Ltd Business Cards

We need a business card with our business logo. We provide window and door installations on high-rises in west coast British Colombia, Canada.

I would like my business information and details on one side of the card, and the other side the company name with logo

Target Market(s)

General Contractors

Industry/Entity Type

Construction

Contact Information for Business Card

one side i want my company name and logo in the dark theme logo that i provided

Requirements
Must have
• Marco Peltieri, 16045518293, RWTFittings@mailbox-demo.com, 1407-5194 Linden Row Burnaby BC, V5H 2K9, Owner & Manager

```html
<!DOCTYPE html>
<html lang="en">
<head>
<meta charset="utf-8">
<title>RWT Fittings Ltd – Business Cards</title>
<link href="https://fonts.googleapis.com/css2?family=Open+Sans:wght@400;600;700&display=swap" rel="stylesheet">
<style>
  :root {
    --page: #232323;
    --card: #141414;
    --card-edge: #29a8e0;
    --accent: #29a8e0;
    --text: #f2f2f2;
    --muted: #9a9a9a;
    --pattern-light: #2e2e2e;
    --pattern-dark: #101010;
  }
  * { margin: 0; padding: 0; box-sizing: border-box; }
  html, body {
    width: 1200px; height: 780px; overflow: hidden;
    background: var(--page);
    font-family: "Open Sans", Arial, sans-serif;
    color: var(--text);
  }
  .canvas { position: relative; width: 1200px; height: 780px; }

  .card {
    position: absolute;
    width: 540px; height: 310px;
    background: var(--card);
    border: 2px solid var(--card-edge);
    border-top-color: #1c1c1c;
    border-right-color: #1c1c1c;
    border-radius: 24px;
    overflow: hidden;
    box-shadow: 0 18px 40px rgba(0,0,0,.55);
  }
  .card--back { left: 50px; top: 100px; }
  .card--front { left: 610px; top: 370px; }

  /* back side */
  .back-pattern {
    position: absolute; inset: 0;
    background: linear-gradient(135deg, var(--pattern-light) 0%, #1d1d1d 45%, var(--pattern-dark) 100%);
  }
  .back-name {
    position: absolute; left: 50%; top: 50%;
    transform: translate(-50%, -50%);
    display: flex; align-items: center; gap: 10px;
    white-space: nowrap;
  }
  .back-name .mark-square { width: 18px; height: 18px; background: var(--muted); }
  .back-name .company { font-size: 22px; font-weight: 700; color: var(--accent); }

  /* front side */
  .front-decor {
    position: absolute; right: 20px; top: 30px;
    width: 220px; height: 220px;
    background: radial-gradient(circle at 50% 50%, #1d1d1d 0%, var(--card) 70%);
  }
  .brand {
    position: absolute; left: 28px; top: 34px;
    display: flex; align-items: center; gap: 12px;
    white-space: nowrap;
  }
  .brand .mark-square { width: 30px; height: 30px; background: var(--muted); }
  .brand .company { font-size: 24px; font-weight: 700; color: var(--accent); line-height: 1; }

  .person {
    position: absolute; right: 28px; top: 40px;
    display: flex; align-items: stretch; gap: 10px;
    text-align: right; white-space: nowrap;
  }
  .person .name { font-size: 19px; font-weight: 700; color: var(--accent); letter-spacing: .5px; text-transform: uppercase; line-height: 1.1; }
  .person .title { font-size: 13px; color: var(--text); margin-top: 2px; }
  .person .bar { width: 9px; background: var(--accent); }

  .address {
    position: absolute; left: 60px; top: 130px;
    font-size: 13.5px; line-height: 1.45; font-style: normal;
  }
  .contacts {
    position: absolute; left: 60px; bottom: 32px;
    list-style: none; font-size: 13.5px; line-height: 1.55;
  }
  .contacts li { display: flex; align-items: center; gap: 8px; }
  .contacts svg { width: 12px; height: 12px; fill: var(--accent); flex: none; }
</style>
</head>
<body>
<main class="canvas">

  <section class="card card--back" aria-label="Card back">
    <div class="back-pattern" role="img" aria-label="Repeating dark building pattern covering the card"></div>
    <div class="back-name">
      <span class="mark-square"></span>
      <span class="company">RWT Fittings Ltd</span>
    </div>
  </section>

  <section class="card card--front" aria-label="Card front">
    <div class="front-decor" role="img" aria-label="Faint large building decoration"></div>

    <div class="brand">
      <span class="mark-square"></span>
      <span class="company">RWT Fittings Ltd</span>
    </div>

    <div class="person">
      <div>
        <p class="name">Marco Peltieri</p>
        <p class="title">Owner &amp; Manager</p>
      </div>
      <span class="bar"></span>
    </div>

    <address class="address">
      1407-5194 Linden Row<br>Burnaby BC, V5H 2K9
    </address>

    <ul class="contacts">
      <li>
        <svg viewBox="0 0 24 24"><path d="M6.6 10.8a15 15 0 0 0 6.6 6.6l2.2-2.2c.3-.3.7-.4 1-.2 1.1.4 2.3.6 3.6.6.6 0 1 .4 1 1V20c0 .6-.4 1-1 1A17 17 0 0 1 3 4c0-.6.4-1 1-1h3.5c.6 0 1 .4 1 1 0 1.3.2 2.5.6 3.6.1.3 0 .7-.2 1z"/></svg>
        16045518293
      </li>
      <li>
        <svg viewBox="0 0 24 24"><path d="M2 6h20v1.2l-10 7-10-7z M2 9.6l10 7 10-7V19H2z"/></svg>
        RWTFittings@mailbox-demo.com
      </li>
      <li>
        <svg viewBox="0 0 24 24"><circle cx="12" cy="12" r="10"/></svg>
        www.rwtfittings-demo.com
      </li>
    </ul>
  </section>

</main>
</body>
</html>
```